K7 Services business card design contest. Use logo and create a professional layout.

See attached sample. Please sharpen all text and images, don't want any pix-elated content. We are looking for a clean look that quickly provides the information need. Please include our information provided on the sample card. Please feel free to offer any design changes. Please only user the colors provided: #2D3539 & #FFA500. Do not prefer any images other than the K7 Logo

Target Market(s)

Construction, Architects, General Contractors, residential

Industry/Entity Type

Business

Contact Information for Business Card

Company logo, Name, email, fax & phone

Font styles to use
Other font styles liked:
• Josefin Slab

Requirements
Must have
• Name
• Phone & Fax #'s
• address
• Logo
• Website url: www.kq7services.example
Nice to have
• Font Colors #2D3539 & #FFA400
• We prefer a white background.

```html
<!DOCTYPE html>
<html lang="en">
<head>
<meta charset="utf-8">
<title>K7 Services Business Card</title>
<link href="https://fonts.googleapis.com/css2?family=Montserrat:wght@400;500;600&display=swap" rel="stylesheet">
<style>
  :root {
    --ink: #2D3539;
    --orange: #EE962C;
    --white: #FFFFFF;
    --backdrop: #E6E6E6;
  }
  * { margin: 0; padding: 0; box-sizing: border-box; }
  html, body { width: 1200px; height: 852px; overflow: hidden; }
  body {
    background: var(--backdrop);
    font-family: 'Montserrat', sans-serif;
    color: var(--ink);
    position: relative;
  }
  .card {
    position: absolute;
    width: 520px;
    height: 297px;
    border-radius: 14px;
    overflow: hidden;
    box-shadow: 0 6px 18px rgba(0,0,0,0.18);
  }
  .card-front { left: 340px; top: 108px; background: var(--orange); }
  .card-back { left: 340px; top: 447px; background: var(--white); }

  .brand-block { position: absolute; }
  .brand { display: flex; align-items: center; gap: 12px; }
  .brand-mark { width: 14px; height: 14px; background: var(--ink); flex: none; }
  .brand-name { font-weight: 500; font-size: 34px; line-height: 1; color: var(--ink); letter-spacing: 0.5px; }
  .brand-tagline { font-weight: 400; font-size: 14px; color: var(--ink); margin-top: 8px; letter-spacing: 1px; text-transform: uppercase; }

  .card-front .brand-block { left: 0; width: 100%; top: 118px; text-align: center; }
  .card-front .brand { justify-content: center; }

  .card-back .brand-block { left: 34px; top: 46px; }
  .card-back .brand-mark { width: 11px; height: 11px; }
  .card-back .brand-name { font-size: 24px; }
  .card-back .brand-tagline { font-size: 9.5px; margin-top: 7px; }

  .divider { position: absolute; left: 34px; top: 132px; width: 270px; height: 2px; background: var(--orange); }

  .person { position: absolute; right: 34px; top: 40px; text-align: right; }
  .person-name { color: var(--orange); font-size: 17px; font-weight: 400; }
  .person-title { font-size: 12px; margin-top: 2px; }

  .contact { position: absolute; right: 34px; top: 100px; list-style: none; font-size: 11.5px; line-height: 19px; }
  .contact li { display: flex; justify-content: flex-end; align-items: center; gap: 8px; }
  .contact svg { width: 11px; height: 11px; fill: var(--orange); flex: none; }

  .address { position: absolute; left: 34px; top: 170px; font-size: 11.5px; line-height: 18px; }

  .service-band {
    position: absolute; left: 0; bottom: 0; width: 100%; height: 66px;
    background: var(--orange);
    display: flex; justify-content: flex-end; align-items: flex-start;
    padding: 10px 34px 0 0;
    color: var(--white); font-size: 11.5px; letter-spacing: 0.3px;
  }
</style>
</head>
<body>
  <section class="card card-front">
    <div class="brand-block">
      <div class="brand">
        <span class="brand-mark"></span>
        <span class="brand-name">K7 Services</span>
      </div>
      <div class="brand-tagline">Clear Views From Above</div>
    </div>
  </section>

  <section class="card card-back">
    <div class="brand-block">
      <div class="brand">
        <span class="brand-mark"></span>
        <span class="brand-name">K7 Services</span>
      </div>
      <div class="brand-tagline">Clear Views From Above</div>
    </div>

    <div class="divider"></div>

    <div class="person">
      <div class="person-name">Daniel R. Mercer, MBA</div>
      <div class="person-title">Director of Operations</div>
    </div>

    <ul class="contact">
      <li>(555) 014 - 2290
        <svg viewBox="0 0 12 12"><path d="M2 1h3l1 3-1.5 1a6 6 0 0 0 2.5 2.5L8 6l3 1v3a1 1 0 0 1-1 1A9 9 0 0 1 1 2a1 1 0 0 1 1-1z"/></svg>
      </li>
      <li>(555) 016 - 7731
        <svg viewBox="0 0 12 12"><rect x="3" y="1" width="6" height="3"/><rect x="1" y="5" width="10" height="5" rx="1"/><rect x="3" y="8" width="6" height="3" fill="#fff"/></svg>
      </li>
      <li>www.kq7services.example
        <svg viewBox="0 0 12 12"><circle cx="6" cy="6" r="5"/><path d="M1 6h10M6 1v10" stroke="#fff" stroke-width="1"/></svg>
      </li>
    </ul>

    <div class="address">
      2190 Larkfield Road, Suite<br>
      410-215 Ashford, Georgia, 30099
    </div>

    <div class="service-band">DRONE | WEBCAM | VIDEO</div>
  </section>
</body>
</html>
```